Meridian Crestline Motors *

Professional business cards for our auto wholesale dealership.

Target Market(s)

New and used cars sales managers and middle class to higher end private party buyers.

Industry/Entity Type

Automotive

Contact Information for Business Card

Meridian Crestline Motors
Darnell R Okonski
Owner
(555) 304-6618
mercrestmotors@quillbox.example
Dealer Lic # 48265

Logo Text

Meridian Crestline Motors, Mer Crest Motors, MCM, etc

Font styles to use
Serif
Sans Serif

Colors

Designer to choose colors to be used in the design.

Requirements
Must have
• A professional, but not pretentious, look
Nice to have
• It might be nice to see "MCM" in a shape form i.e. circle, triangle, etc in the corner or background somehwere
Should not have
• bright "girly" colors

```html
<!DOCTYPE html>
<html lang="en">
<head>
<meta charset="utf-8">
<title>Meridian Crestline Motors – Business Card</title>
<link href="https://fonts.googleapis.com/css2?family=Open+Sans:wght@400;600;800&display=swap" rel="stylesheet">
<style>
  :root {
    --page-bg: #3a3d42;
    --card-dark: #1d2127;
    --card-mid: #2c323a;
    --lime: #9fcc14;
    --lime-light: #b7dc1e;
    --ink-white: #ffffff;
    --ink-soft: #d6d9dd;
  }
  * { margin: 0; padding: 0; box-sizing: border-box; }
  html, body { width: 1200px; height: 1200px; overflow: hidden; }
  body {
    background: var(--page-bg);
    font-family: "Open Sans", Arial, sans-serif;
    position: relative;
  }
  .card {
    position: absolute;
    left: 150px;
    width: 900px;
    height: 514px;
    border-radius: 26px;
    overflow: hidden;
    background: radial-gradient(ellipse at 40% 35%, var(--card-mid), var(--card-dark) 75%);
    box-shadow: 0 18px 40px rgba(0,0,0,.45);
  }
  .card::after {
    content: "";
    position: absolute;
    left: 0; right: 0; bottom: 0;
    height: 16px;
    background: var(--lime);
  }
  .card-front { top: 70px; }
  .card-back { top: 630px; }

  /* front */
  .front-mark {
    position: absolute;
    left: 50%;
    top: 70px;
    width: 170px; height: 170px;
    margin-left: -85px;
    border-radius: 50%;
    background: var(--lime);
    display: flex; align-items: center; justify-content: center;
    color: var(--card-dark);
    font-weight: 800;
    font-size: 54px;
    letter-spacing: 1px;
  }
  .front-title {
    position: absolute;
    left: 0; right: 0; top: 270px;
    text-align: center;
    color: var(--ink-white);
  }
  .front-title .primary {
    display: block;
    font-weight: 800;
    font-size: 74px;
    line-height: 1;
    letter-spacing: 1px;
  }
  .front-title .secondary {
    display: block;
    font-weight: 600;
    font-size: 40px;
    margin-top: 6px;
  }

  /* back */
  .back-title {
    position: absolute;
    left: 58px; top: 44px;
    color: var(--ink-white);
  }
  .back-title .primary {
    display: block;
    font-weight: 800;
    font-size: 46px;
    line-height: 1;
  }
  .back-title .secondary {
    display: block;
    font-weight: 600;
    font-size: 26px;
    margin-top: 2px;
  }
  .divider-line {
    position: absolute;
    left: 0; top: 168px;
    width: 900px; height: 4px;
    background: var(--lime);
  }
  .back-mark {
    position: absolute;
    left: 590px; top: 60px;
    width: 220px; height: 220px;
    border-radius: 50%;
    background: var(--lime);
    display: flex; align-items: center; justify-content: center;
    color: var(--card-dark);
    font-weight: 800;
    font-size: 66px;
  }
  .person {
    position: absolute;
    left: 58px; top: 190px;
    display: flex; align-items: flex-start; gap: 14px;
  }
  .person .pill {
    width: 18px; height: 40px;
    border-radius: 9px;
    background: var(--lime);
    margin-top: 4px;
  }
  .person .name {
    color: var(--ink-white);
    font-weight: 600;
    font-size: 30px;
    line-height: 1.1;
  }
  .person .role {
    color: var(--ink-soft);
    font-size: 19px;
  }
  .contacts {
    position: absolute;
    left: 58px; top: 296px;
    list-style: none;
    color: var(--ink-soft);
    font-size: 18px;
  }
  .contacts li {
    display: flex; align-items: center; gap: 12px;
    margin-bottom: 14px;
  }
  .contacts svg { width: 18px; height: 18px; flex: none; }
  .contacts .license { padding-left: 0; }
</style>
</head>
<body>

<section class="card card-front" aria-label="Card front">
  <div class="front-mark">MCM</div>
  <h1 class="front-title">
    <span class="primary">MERIDIAN</span>
    <span class="secondary">Crestline Motors</span>
  </h1>
</section>

<section class="card card-back" aria-label="Card back">
  <div class="divider-line"></div>
  <div class="back-mark">MCM</div>
  <h2 class="back-title">
    <span class="primary">MERIDIAN</span>
    <span class="secondary">Crestline Motors</span>
  </h2>
  <div class="person">
    <span class="pill"></span>
    <div>
      <div class="name">Darnell R Okonski</div>
      <div class="role">Owner</div>
    </div>
  </div>
  <ul class="contacts">
    <li>
      <svg viewBox="0 0 24 24" aria-hidden="true"><path fill="#9fcc14" d="M6.6 10.8a15.1 15.1 0 0 0 6.6 6.6l2.2-2.2a1 1 0 0 1 1-.25 11.4 11.4 0 0 0 3.6.57 1 1 0 0 1 1 1V20a1 1 0 0 1-1 1A17 17 0 0 1 3 4a1 1 0 0 1 1-1h3.5a1 1 0 0 1 1 1c0 1.25.2 2.45.57 3.57a1 1 0 0 1-.25 1z"/></svg>
      (555) 304-6618
    </li>
    <li>
      <svg viewBox="0 0 24 24" aria-hidden="true"><rect x="2.5" y="5" width="19" height="14" fill="none" stroke="#9fcc14" stroke-width="2"/><path d="M3 6l9 7 9-7" fill="none" stroke="#9fcc14" stroke-width="2"/></svg>
      mercrestmotors@quillbox.example
    </li>
    <li class="license">Dealer Lic # 48265</li>
  </ul>
</section>

</body>
</html>
```